Melorix artwork for new single release

I need Melorix artwork creating to release a new single on there.

The specs are:

Ideal size: 3000 x 3000 pixels
Minimum size: 1400 x 1400 pixels
Aspect ratio: 1:1 (must be a perfect square)
File format: JPG or PNG
Color space: sRGB
File size: Max 4MB

The song is called "Was It Ever Rain?"
The artist is "Martin Hollow"

We have no images of Martin, so it really is open to imagination.

Target Market(s)

Melorix listeners

Industry/Entity Type

Music

```html
<!DOCTYPE html>
<html lang="en">
<head>
<meta charset="utf-8">
<title>Was It Ever Rain? – Martin Hollow</title>
<link rel="stylesheet" href="https://fonts.googleapis.com/css2?family=Bevan&family=Playfair+Display:wght@700;800&display=swap">
<style>
  :root {
    --bg: #130e0c;
    --ink: #f2f0ee;
    --accent: #c4141a;
    --artist: #b93c1c;
    --flame-core: #ffe6a6;
    --flame-mid: #f29a2e;
    --flame-edge: #7a2a08;
    --rose: #b3141c;
  }
  * { margin: 0; padding: 0; box-sizing: border-box; }
  html, body {
    width: 1200px; height: 1200px; overflow: hidden; background: var(--bg);
  }
  .cover {
    position: relative; width: 1200px; height: 1200px; overflow: hidden;
    background: var(--bg);
  }
  .cover-photo { position: absolute; inset: 0; width: 1200px; height: 1200px; }

  .title-lead {
    position: absolute; left: 232px; top: 418px;
    font-family: "Playfair Display", serif; font-weight: 800;
    font-size: 30px; letter-spacing: 0.01em; color: var(--ink);
  }
  .glyph {
    position: absolute; width: 150px; height: 142px;
    display: flex; align-items: center; justify-content: center;
    font-family: "Bevan", serif; font-size: 178px; line-height: 1;
    color: var(--ink);
  }
  .glyph--accent { color: var(--accent); }
  .glyph--question { width: 110px; font-size: 170px; color: var(--accent); }

  .artist-name {
    position: absolute; left: 0; right: 0; top: 1090px;
    padding-left: 330px;
    text-align: center;
    font-family: "Playfair Display", serif; font-weight: 700;
    font-size: 36px; letter-spacing: 0.38em; color: var(--artist);
  }
</style>
</head>
<body>
<main class="cover">
  <svg class="cover-photo" viewBox="0 0 1200 1200" role="img" aria-label="Photograph of a single red rose burning, with tall orange flames rising from the bloom against a dark background">
    <defs>
      <radialGradient id="flameGlow" cx="0.5" cy="0.5" r="0.5">
        <stop offset="0" stop-color="var(--flame-core)"/>
        <stop offset="0.45" stop-color="var(--flame-mid)"/>
        <stop offset="0.8" stop-color="var(--flame-edge)" stop-opacity="0.5"/>
        <stop offset="1" stop-color="var(--bg)" stop-opacity="0"/>
      </radialGradient>
      <radialGradient id="roseGlow" cx="0.5" cy="0.5" r="0.5">
        <stop offset="0" stop-color="var(--rose)"/>
        <stop offset="0.7" stop-color="#6e0b10"/>
        <stop offset="1" stop-color="var(--bg)" stop-opacity="0"/>
      </radialGradient>
    </defs>
    <rect width="1200" height="1200" fill="var(--bg)"/>
    <ellipse cx="430" cy="470" rx="240" ry="430" fill="url(#flameGlow)"/>
    <ellipse cx="490" cy="880" rx="170" ry="150" fill="url(#roseGlow)"/>
  </svg>

  <h1 class="title" aria-label="Was It Ever Rain?">
    <span class="title-lead" aria-hidden="true">WAS IT</span>
    <span class="glyph" style="left:320px; top:460px" aria-hidden="true">E</span>
    <span class="glyph glyph--accent" style="left:470px; top:460px" aria-hidden="true">V</span>
    <span class="glyph" style="left:620px; top:460px" aria-hidden="true">E</span>
    <span class="glyph" style="left:770px; top:460px" aria-hidden="true">R</span>
    <span class="glyph" style="left:770px; top:606px" aria-hidden="true">A</span>
    <span class="glyph" style="left:770px; top:752px" aria-hidden="true">I</span>
    <span class="glyph" style="left:770px; top:898px" aria-hidden="true">N</span>
    <span class="glyph glyph--question" style="left:918px; top:930px" aria-hidden="true">?</span>
  </h1>

  <p class="artist-name">Martin Hollow</p>
</main>
</body>
</html>
```